New business card for a regional office of a US M&A company

We need business card for a finance company, office based in Hong Kong , our Head office is in US, our business is to Merge and acquires companies , the new office will be a regional office for the Asia Pacific region. We want to use the head office logo as attached ( but don't have to be exactly the same, can be a variation to it) as a base and then add Asia Pacific alongside the logo.
We would prefer to have be bilingual Eng + Chinese, although we don't really have Chinese company name .

Industry/Entity Type

Business

Contact Information for Business Card

Clara Jo Tsang
 

VP,
APAC M&A Operations
Eli Global Asia Pacific Limited
 
Unit 1407, K18
18 Tai Lok Shan Road, 
Hong Kong 
 
M: +852 6038 1742
T : +852 2836 4100
F : +852 2836 4177
VOIP: 4158
 
cjtsang@orinvantage.com

Font styles to use
Serif
Sans Serif

Colors

Designer to choose colors to be used in the design.

Requirements
Must have
• APAC Office

```html
<!DOCTYPE html>
<html lang="en">
<head>
<meta charset="utf-8">
<title>Orin Vantage Asia Pacific – Business Card</title>
<link rel="stylesheet" href="https://fonts.googleapis.com/css2?family=Open+Sans:wght@400;600;700;800&display=swap">
<style>
  :root {
    --backdrop: #3b3c3e;
    --card: #1c1d20;
    --card-edge: #26272b;
    --accent: #2aa8d6;
    --ink: #f2f2f2;
    --emboss: #4a4b50;
    --mark: #ffffff;
  }
  * { margin: 0; padding: 0; box-sizing: border-box; }
  html, body {
    width: 799px; height: 1200px; overflow: hidden;
    background: var(--backdrop);
    font-family: "Open Sans", sans-serif;
  }
  .canvas {
    position: relative; width: 799px; height: 1200px;
  }
  .card {
    position: absolute; left: 100px; width: 600px; height: 340px;
    background: var(--card);
    border: 1px solid var(--card-edge);
    border-radius: 4px;
    box-shadow: 0 14px 30px rgba(0,0,0,.45);
    overflow: hidden;
  }
  .card--front { top: 150px; }
  .card--back  { top: 710px; }

  /* Front */
  .brand {
    position: absolute; inset: 0;
    display: flex; align-items: center; justify-content: center; gap: 18px;
  }
  .brand__square {
    width: 34px; height: 34px; background: var(--emboss);
  }
  .brand__name {
    font-weight: 800; font-size: 44px; letter-spacing: 1px;
    color: var(--emboss);
  }

  /* Back */
  .back__square {
    position: absolute; left: 34px; top: 70px;
    width: 190px; height: 190px; background: var(--mark);
  }
  .details {
    position: absolute; left: 300px; top: 62px; right: 24px;
    color: var(--ink);
  }
  .details__name {
    font-weight: 700; font-size: 23px; color: var(--accent); line-height: 1.1;
  }
  .details__title {
    font-size: 13px; line-height: 1.35; margin-top: 4px;
  }
  .details__company {
    font-weight: 700; font-size: 15px; color: var(--accent); margin-top: 16px;
  }
  .contact {
    list-style: none; margin-top: 6px; font-size: 13.5px; line-height: 1.45;
  }
  .contact li { display: flex; align-items: center; gap: 8px; }
  .contact svg { width: 12px; height: 12px; fill: var(--accent); flex: none; }
  .contact__voip { color: var(--accent); margin-left: 6px; }
  .address { font-size: 13.5px; line-height: 1.45; margin-top: 2px; }
</style>
</head>
<body>
<main class="canvas">

  <section class="card card--front" aria-label="Card front">
    <div class="brand">
      <span class="brand__square"></span>
      <span class="brand__name">ORIN VANTAGE</span>
    </div>
  </section>

  <section class="card card--back" aria-label="Card back">
    <div class="back__square"></div>
    <div class="details">
      <h1 class="details__name">Clara Jo Tsang</h1>
      <p class="details__title">Vice President,<br>APAC M&amp;A Operations</p>
      <p class="details__company">Orin Vantage Asia Pacific Limited</p>
      <ul class="contact">
        <li>
          <svg viewBox="0 0 12 12" aria-hidden="true"><rect x="3" y="0" width="6" height="12" rx="1"/></svg>
          +852 6038 1742
        </li>
        <li>
          <svg viewBox="0 0 12 12" aria-hidden="true"><path d="M1 4 Q6 0 11 4 L9 6 L7.5 4.5 L4.5 4.5 L3 6 Z M2 7 H10 V11 H2 Z"/></svg>
          +852 2836 4100
        </li>
        <li>
          <svg viewBox="0 0 12 12" aria-hidden="true"><rect x="3" y="0" width="6" height="4"/><rect x="0" y="4" width="12" height="6" rx="1"/></svg>
          +852 2836 4177, <span class="contact__voip">VOIP:</span> 4158
        </li>
        <li>
          <svg viewBox="0 0 12 12" aria-hidden="true"><path d="M0 2 H12 V10 H0 Z M0 2 L6 7 L12 2" /></svg>
          cjtsang@orinvantage.com
        </li>
      </ul>
      <p class="address">Unit: 1407, K18 18, Tai Lok Shan<br>Road, Hong Kong</p>
    </div>
  </section>

</main>
</body>
</html>
```